Real Estate Wordpress Landing Page

I'm looking to a landing page dedicated to my real estate brokerage that's catered to promoting that my company provides 1.5% listings to home sellers... I have a couple examples that I'm really looking towards mocking in a version with similar color schemes using my current company colors/website.

http://harbelo.com/
https://www.quarvantis.com/about/one-percent-listing-fee

My brokerage company website is http://www.brightmarrow.us/

Target Market(s)

real estate home sellers & buyers

Industry/Entity Type

Real Estate

Coding

Coded - Design and coding required

Number of Pages Required

1 page

Colors
3176b5
0255a3
eaf1f7
cedeed

Requirements
Must have
• Company website colors - http://www.brightmarrow.us/
• Something around the lines of this website page - http://harbelo.com/
• Wordpress compatibility

```html
<!DOCTYPE html>
<html lang="en">
<head>
<meta charset="utf-8">
<title>Bright Marrow Realty – List for 1.5% Commission</title>
<link rel="stylesheet" href="https://fonts.googleapis.com/css2?family=Poppins:ital,wght@0,400;0,500;0,600;0,700;1,400&display=swap">
<style>
:root{
  --blue:#0a3f9a;
  --blue-bright:#0255a3;
  --blue-soft:#3176b5;
  --ice:#eaf1f7;
  --mist:#cedeed;
  --grey-bg:#eeeef0;
  --ink:#1c1c1c;
  --text:#555;
  --dark:#1a1a1a;
  --white:#fff;
}
*{box-sizing:border-box;margin:0;padding:0}
html,body{width:1200px;height:3782px;overflow:hidden}
body{position:relative;font-family:'Poppins',sans-serif;color:var(--ink);background:var(--white)}
.abs{position:absolute}
a{color:inherit;text-decoration:none}

/* header */
.site-header{left:0;top:0;width:1200px;height:181px;background:var(--white)}
.brand{left:96px;top:54px;display:flex;align-items:center;gap:12px}
.brand-mark{width:26px;height:26px;background:var(--blue)}
.brand-name{font-size:22px;font-weight:600;color:var(--ink)}
.contact-item{font-size:13px;color:var(--ink);display:flex;align-items:center;gap:7px;white-space:nowrap}
.contact-item svg{width:13px;height:13px;fill:var(--blue)}
.contact-sub{font-size:13px;color:var(--ink);white-space:nowrap}
.main-nav{left:88px;top:144px;width:1026px;height:75px;background:var(--blue);z-index:5;display:flex;align-items:center;padding-left:83px}
.nav-home{position:absolute;left:0;top:0;width:150px;height:75px}
.main-nav ul{list-style:none;display:flex;gap:22px;position:relative}
.main-nav li{font-size:13px;color:var(--white);font-weight:400;white-space:nowrap}
.main-nav li.active{color:var(--blue);font-weight:500}

/* hero */
.hero{left:0;top:181px;width:1200px;height:706px;clip-path:polygon(0 0,100% 0,100% 605px,50% 706px,0 605px)}
.hero-photo{width:100%;height:100%;background:linear-gradient(180deg,#5c5f63 0%,#797b7d 40%,#4b4d50 100%)}
.hero-shade{left:0;top:0;width:100%;height:100%;background:rgba(20,22,28,.45)}
.hero-brand{left:0;width:1200px;top:440px;text-align:center;color:var(--white);font-size:16px;font-weight:600;display:flex;justify-content:center;align-items:center;gap:10px}
.hero-brand span.sq{width:16px;height:16px;background:var(--white)}
.hero-title{left:0;width:1200px;top:490px;text-align:center;color:var(--white);font-size:40px;font-weight:700;letter-spacing:.5px}
.hero-sub{left:0;width:1200px;top:548px;text-align:center;color:var(--white);font-size:28px;font-weight:600}
.field{height:34px;background:var(--white);font-size:13px;color:#888;display:flex;align-items:center;justify-content:space-between;padding:0 14px}
.field .caret{width:0;height:0;border-left:5px solid transparent;border-right:5px solid transparent;border-top:7px solid #222}
.search-btn{height:34px;background:var(--blue);color:var(--white);font-size:14px;font-weight:600;display:flex;align-items:center;justify-content:center}

/* services */
.services{left:0;top:787px;width:1200px;height:600px;background:var(--grey-bg);z-index:-1}
.service{width:292px;height:215px;background:var(--white);box-shadow:0 2px 8px rgba(0,0,0,.12);text-align:center;padding:52px 24px 0}
.service.featured{background:var(--blue)}
.service h3{font-size:19px;font-weight:600;color:var(--blue);line-height:1.5;text-transform:uppercase}
.service.featured h3,.service.featured p{color:var(--white)}
.service p{font-size:14px;color:var(--text);line-height:1.6;margin-top:6px}
.service-icon{width:76px;height:76px;border-radius:50%;background:var(--blue);border:4px solid var(--white);display:flex;align-items:center;justify-content:center}
.service-icon svg{width:36px;height:36px;stroke:var(--white);fill:none;stroke-width:2}

/* featured properties */
.properties{left:0;top:1285px;width:1200px;height:701px;clip-path:polygon(0 96px,50% 0,100% 96px,100% 100%,0 100%)}
.properties-photo{width:100%;height:100%;background:linear-gradient(90deg,#3a3533 0%,#2a2a2c 45%,#45403c 100%)}
.properties-shade{left:0;top:0;width:100%;height:100%;background:rgba(0,0,0,.45)}
.section-title{font-size:26px;font-weight:600;color:var(--white);text-align:center;width:1200px;left:0}
.prop-photo{width:287px;height:174px;border:3px solid var(--white)}
.tag{right:8px;top:8px;background:var(--blue);color:var(--white);font-size:11px;font-weight:500;padding:5px 10px;border-radius:12px}
.prop h4{font-size:14px;font-weight:600;color:var(--white);text-transform:uppercase}
.prop .meta{font-size:11px;color:var(--white);margin-top:10px;display:flex;gap:14px}
.prop p{font-size:13px;color:#e6e6e6;line-height:1.6;margin-top:8px}
.prop .more{font-size:13px;color:var(--white);font-weight:600;text-decoration:underline;margin-top:10px;display:block}
.dot{width:14px;height:14px;border-radius:50%;background:var(--white)}
.dot.hollow{background:transparent;border:2px solid var(--white)}

/* categories */
.category{width:323px;height:217px;background:var(--white);box-shadow:0 2px 10px rgba(0,0,0,.15);padding:40px 28px 0}
.category.featured{background:var(--blue)}
.category .head{display:flex;align-items:center;gap:22px}
.category svg{width:76px;height:70px;fill:none;stroke:var(--blue);stroke-width:2.4}
.category.featured svg{stroke:var(--white)}
.category h3{font-size:17px;font-weight:600;color:var(--blue);text-transform:uppercase}
.category.featured h3,.category.featured p{color:var(--white)}
.category p{font-size:12.5px;color:var(--text);line-height:1.6;text-align:center;margin-top:12px}

/* testimonials */
.testimonials{left:0;top:2444px;width:1200px;height:454px;clip-path:polygon(0 0,100% 0,100% 391px,50% 100%,0 391px)}
.testimonials-photo{width:100%;height:100%;background:linear-gradient(90deg,#252628 0%,#3c3d40 50%,#2a2b2e 100%)}
.quote-mark{font-size:44px;color:var(--white);font-family:Georgia,serif;line-height:1}
.quote{left:215px;width:780px;top:2616px;font-size:11.5px;font-style:italic;color:var(--white);text-align:center;line-height:1.7}
.avatar{left:508px;top:2690px;width:88px;height:88px;border-radius:50%;background:linear-gradient(135deg,#8a7768,#5d5049);border:3px solid var(--white)}
.author{left:612px;top:2722px;color:var(--white)}
.author b{font-size:11px;font-weight:500;display:block}
.author span{font-size:10px;font-style:italic}
.small-dot{width:8px;height:8px;border-radius:50%;border:1.5px solid var(--white)}

/* events */
.events-title{left:101px;top:2950px;font-size:26px;font-weight:700;color:var(--blue)}
.event-photo{background:linear-gradient(135deg,#c9c9c9,#e6e2dc 50%,#b53a3a)}
.date{font-size:12px;color:var(--blue);display:flex;align-items:center;gap:8px}
.date svg{width:14px;height:14px;fill:var(--blue)}
.event-text{font-size:11.5px;color:var(--text);line-height:1.65}
.link-more{font-size:12px;font-weight:700;color:var(--blue)}
.event-item h4{font-size:14px;font-weight:600;color:var(--blue);text-transform:uppercase}

/* footer */
.site-footer{left:0;top:3350px;width:1200px;height:432px;background:var(--dark);clip-path:polygon(0 0,50% 50px,100% 0,100% 100%,0 100%)}
.footer-col h5{font-size:17px;font-weight:600;color:var(--white);text-transform:uppercase}
.footer-col p{font-size:13px;color:#d8d8d8;line-height:1.75;margin-top:20px}
.footer-col ul{list-style:none;margin-top:18px}
.footer-col li{font-size:12.5px;color:#d8d8d8;line-height:24.5px;display:flex;align-items:center;gap:18px}
.footer-col li::before{content:"";width:0;height:0;border-top:4px solid transparent;border-bottom:4px solid transparent;border-left:6px solid #d8d8d8}
.footer-read{font-size:13px;color:var(--white);text-decoration:underline;margin-top:16px;display:block}
.email-field{width:292px;height:38px;background:var(--white);font-size:12px;color:#888;padding:0 12px;display:flex;align-items:center;margin-top:28px}
.subscribe{width:130px;height:38px;border-radius:19px;background:var(--blue);color:var(--white);font-size:13px;font-weight:500;display:flex;align-items:center;justify-content:center;margin-top:18px}
.copyright{left:0;width:1200px;top:3724px;text-align:center;font-size:12px;color:#d8d8d8}
.footer-rule{left:101px;top:3692px;width:1000px;height:1px;background:#444}
</style>
</head>
<body>

<header class="site-header abs">
  <div class="brand abs"><span class="brand-mark"></span><span class="brand-name">Bright Marrow Realty</span></div>

  <div class="contact-item abs" style="left:578px;top:56px"><svg viewBox="0 0 24 24"><path d="M12 2a7 7 0 0 0-7 7c0 5 7 13 7 13s7-8 7-13a7 7 0 0 0-7-7zm0 9.5A2.5 2.5 0 1 1 12 6.5a2.5 2.5 0 0 1 0 5z"/></svg>420 Lantern Cove, Ste 310</div>
  <div class="contact-sub abs" style="left:596px;top:86px">Coral Mesa, FL 33180</div>

  <div class="contact-item abs" style="left:802px;top:56px"><svg viewBox="0 0 24 24"><path d="M6.6 10.8a15 15 0 0 0 6.6 6.6l2.2-2.2a1 1 0 0 1 1-.25 11 11 0 0 0 3.6.6 1 1 0 0 1 1 1V20a1 1 0 0 1-1 1A17 17 0 0 1 3 4a1 1 0 0 1 1-1h3.5a1 1 0 0 1 1 1 11 11 0 0 0 .6 3.6 1 1 0 0 1-.25 1z"/></svg>Call us</div>
  <div class="contact-sub abs" style="left:822px;top:86px">561-555-0148</div>

  <div class="contact-item abs" style="left:926px;top:56px"><svg viewBox="0 0 24 24"><path d="M2 5h20v2l-10 6L2 7zm0 4l10 6 10-6v10H2z"/></svg>Email us</div>
  <div class="contact-sub abs" style="left:946px;top:86px">contact@brightmarrow.us</div>
</header>

<nav class="main-nav abs">
  <svg class="nav-home" viewBox="0 0 150 75"><polygon points="38,0 150,0 112,75 0,75" fill="#fff"/></svg>
  <ul>
    <li class="active">Home</li><li>Featured Cities</li><li>Property Search</li><li>Email Alerts</li><li>Communities</li><li>Buyers &amp; Sellers</li><li>Rentals</li><li>Investing</li><li>Contact</li>
  </ul>
</nav>

<section class="hero abs">
  <div class="hero-photo" role="img" aria-label="Bright modern living room and kitchen interior"></div>
  <div class="hero-shade abs"></div>
</section>
<svg class="abs" style="left:0;top:781px;z-index:3" width="1200" height="110"><polyline points="0,5 600,106 1200,5" fill="none" stroke="#0a3f9a" stroke-width="4"/></svg>

<div class="hero-brand abs"><span class="sq"></span>Bright Marrow Realty</div>
<h1 class="hero-title abs">LIST FOR 1.5% COMMISSION</h1>
<p class="hero-sub abs">and Receive Top Marketing from Real Estate Pro!</p>

<div class="field abs" style="left:128px;top:607px;width:217px">Location</div>
<div class="field abs" style="left:370px;top:607px;width:215px">Property Type<span class="caret"></span></div>
<div class="field abs" style="left:615px;top:607px;width:212px">Min. Price<span class="caret"></span></div>
<div class="field abs" style="left:854px;top:607px;width:214px">Max. Price<span class="caret"></span></div>
<div class="field abs" style="left:247px;top:675px;width:217px">Beds<span class="caret"></span></div>
<div class="field abs" style="left:494px;top:675px;width:214px">Baths<span class="caret"></span></div>
<div class="search-btn abs" style="left:736px;top:675px;width:214px">Search</div>

<section class="services abs"></section>

<div class="service abs" style="left:111px;top:1000px">
  <h3>Sell with Bright Marrow &amp; Save $$$</h3>
  <p>Sed ut perspiciatis unde omnis iste natus error sit voluptatem</p>
</div>
<div class="service featured abs" style="left:456px;top:1000px">
  <h3>Start your home search with us</h3>
  <p>Sed ut perspiciatis unde omnis iste natus error sit voluptatem</p>
</div>
<div class="service abs" style="left:796px;top:1000px">
  <h3>Leasing &amp; Property Management</h3>
  <p>Sed ut perspiciatis unde omnis iste natus error sit voluptatem</p>
</div>
<div class="service-icon abs" style="left:219px;top:960px"><svg viewBox="0 0 36 36"><rect x="6" y="14" width="16" height="16"/><path d="M4 16 14 7l10 9"/><circle cx="27" cy="24" r="6"/><path d="M27 21v6"/></svg></div>
<div class="service-icon abs" style="left:564px;top:960px"><svg viewBox="0 0 36 36"><rect x="5" y="5" width="22" height="22"/><circle cx="18" cy="18" r="7"/><path d="M23 23l8 8"/></svg></div>
<div class="service-icon abs" style="left:904px;top:960px"><svg viewBox="0 0 36 36"><path d="M5 17 18 6l13 11"/><path d="M9 14v16h18V14"/><rect x="15" y="20" width="6" height="10"/></svg></div>

<section class="properties abs">
  <div class="properties-photo" role="img" aria-label="Agent shaking hands with home buyers"></div>
  <div class="properties-shade abs"></div>
</section>
<svg class="abs" style="left:0;top:1281px;z-index:3" width="1200" height="104"><polyline points="0,100 600,4 1200,100" fill="none" stroke="#0a3f9a" stroke-width="4"/></svg>

<h2 class="section-title abs" style="top:1440px">Featured Properties</h2>

<article class="prop abs" style="left:149px;top:1552px;width:287px">
  <div class="prop-photo" role="img" aria-label="Couple in front of a modern house"></div>
  <span class="tag abs">SOLD</span>
  <h4 style="margin-top:18px">Sold | 76 Willowby Road</h4>
  <div class="meta"><span>▪ 3 ▪ 3</span></div>
  <p>Sed ut perspiciatis unde omnis iste natus error sit voluptatem accusantium.</p>
  <a class="more">Read More</a>
</article>
<article class="prop abs" style="left:456px;top:1552px;width:290px">
  <div class="prop-photo" role="img" aria-label="Agent meeting buyers beside a for sale sign"></div>
  <span class="tag abs">$ 4,380,000</span>
  <h4 style="margin-top:18px">145 Orrin Avenue</h4>
  <div class="meta"><span>▪ 2 ▪ 3</span></div>
  <p>Sed ut perspiciatis unde omnis iste natus error sit voluptatem accusantium.</p>
  <a class="more">Read More</a>
</article>
<article class="prop abs" style="left:769px;top:1552px;width:287px">
  <div class="prop-photo" role="img" aria-label="Agent handing keys to a buyer outside a brick house"></div>
  <span class="tag abs">SOLD</span>
  <h4 style="margin-top:18px">Sold | 19 Fennick Road</h4>
  <div class="meta"><span>▪ 4 ▪ 3</span></div>
  <p>Sed ut perspiciatis unde omnis iste natus error sit voluptatem accusantium.</p>
  <a class="more">Read More</a>
</article>

<div class="dot hollow abs" style="left:569px;top:1918px"></div>
<div class="dot abs" style="left:592px;top:1918px"></div>
<div class="dot abs" style="left:615px;top:1918px"></div>

<article class="category abs" style="left:93px;top:2109px">
  <div class="head"><svg viewBox="0 0 76 70"><rect x="8" y="10" width="28" height="56"/><rect x="36" y="24" width="32" height="42"/><path d="M14 18h6M24 18h6M14 28h6M24 28h6M14 38h6M24 38h6M14 48h6M24 48h6M42 32h6M56 32h6M42 42h6M56 42h6M42 52h6M56 52h6"/></svg><h3>Apartments</h3></div>
  <p>Lorem ipsum dolor sit amet, consectetur adipiscing elit, sed do eiusmod tempor incididunt ut labore</p>
</article>
<article class="category featured abs" style="left:433px;top:2109px;width:331px">
  <div class="head"><svg viewBox="0 0 76 70"><path d="M4 32 38 6l34 26"/><path d="M12 26v40h52V26"/><rect x="20" y="36" width="14" height="12"/><rect x="42" y="36" width="14" height="12"/><path d="M4 66h68"/></svg><h3>Houses</h3></div>
  <p>Lorem ipsum dolor sit amet, consectetur adipiscing elit, sed do eiusmod tempor incididunt ut labore</p>
</article>
<article class="category abs" style="left:776px;top:2109px;width:330px">
  <div class="head"><svg viewBox="0 0 76 70"><path d="M8 36h60v30H8z"/><path d="M4 36l8-12h52l8 12"/><rect x="30" y="46" width="16" height="20"/><circle cx="38" cy="14" r="9"/><path d="M35 14h6"/></svg><h3>Commercial</h3></div>
  <p>Lorem ipsum dolor sit amet, consectetur adipiscing elit, sed do eiusmod tempor incididunt ut labore</p>
</article>

<section class="testimonials abs">
  <div class="testimonials-photo" role="img" aria-label="Smiling happy homeowner in soft focus"></div>
</section>
<svg class="abs" style="left:0;top:2831px;z-index:3" width="1200" height="72"><polyline points="0,4 600,67 1200,4" fill="none" stroke="#0a3f9a" stroke-width="4"/></svg>

<h2 class="section-title abs" style="top:2556px;font-size:25px">TESTIMONIALS</h2>
<span class="quote-mark abs" style="left:192px;top:2604px">“</span>
<p class="quote abs">Lorem ipsum is simply dummy text of the printing and typesetting industry. Lorem ipsum has been the industry's standard dummy text ever since the 1500s, when an unknown printer took a galley of type and scrambled it to make a type specimen book.</p>
<span class="quote-mark abs" style="left:966px;top:2650px">”</span>
<div class="avatar abs" role="img" aria-label="Customer portrait"></div>
<div class="author abs"><b>~ DALEN ROURKE</b><span>satisfied customer</span></div>
<div class="small-dot abs" style="left:961px;top:2730px"></div>
<div class="small-dot abs" style="left:973px;top:2730px"></div>

<h2 class="events-title abs">EVENTS</h2>
<div class="event-photo abs" role="img" aria-label="Hand holding keys in front of a for sale sign" style="left:101px;top:3011px;width:370px;height:177px"></div>
<div class="date abs" style="left:101px;top:3206px"><svg viewBox="0 0 16 16"><path d="M2 3h12v11H2zM4 1h2v3H4zM10 1h2v3h-2z"/></svg>JUL 13 / 2018</div>
<p class="event-text abs" style="left:101px;top:3234px;width:380px">Sed ut perspiciatis unde omnis iste natus error sit voluptatem accusantium doloremque laudantium, totam rem aperiam</p>
<a class="link-more abs" style="left:101px;top:3286px">READ MORE &gt;&gt;</a>

<div class="event-photo abs" role="img" aria-label="Couple smiling at home" style="left:559px;top:3006px;width:106px;height:101px;background:linear-gradient(135deg,#b8c2cc,#8e98a4)"></div>
<div class="event-item abs" style="left:693px;top:3004px;width:410px">
  <h4>Lorem Ipsum</h4>
  <div class="date" style="margin-top:8px"><svg viewBox="0 0 16 16"><path d="M2 3h12v11H2zM4 1h2v3H4zM10 1h2v3h-2z"/></svg>JUL 17 / 2018</div>
  <p class="event-text" style="margin-top:6px">Sed ut perspiciatis unde omnis iste natus error sit voluptatem accusantium doloremque laudantium, totam rem aperiam</p>
</div>
<div class="abs" style="left:559px;top:3127px;width:540px;height:1px;background:#ddd"></div>
<div class="event-photo abs" role="img" aria-label="Person holding house keys at a doorway" style="left:559px;top:3147px;width:106px;height:101px;background:linear-gradient(135deg,#d9d4cc,#9a948c)"></div>
<div class="event-item abs" style="left:693px;top:3145px;width:410px">
  <h4>Lorem Ipsum</h4>
  <div class="date" style="margin-top:8px"><svg viewBox="0 0 16 16"><path d="M2 3h12v11H2zM4 1h2v3H4zM10 1h2v3h-2z"/></svg>JUN 21 / 2018</div>
  <p class="event-text" style="margin-top:6px">Sed ut perspiciatis unde omnis iste natus error sit voluptatem accusantium doloremque laudantium, totam rem aperiam</p>
</div>
<a class="link-more abs" style="left:561px;top:3290px">VIEW MORE &gt;&gt;</a>

<footer class="site-footer abs"></footer>
<svg class="abs" style="left:0;top:3346px;z-index:3" width="1200" height="58"><polyline points="0,4 600,54 1200,4" fill="none" stroke="#0a3f9a" stroke-width="4"/></svg>

<div class="footer-col abs" style="left:101px;top:3460px;width:240px">
  <h5>About Company</h5>
  <p>Lorem ipsum dolor sit amet, consectetur adipiscing elit, sed do eiusmod tempor incididunt ut laboreet dolore magna aliqua.</p>
  <a class="footer-read">READ MORE</a>
</div>
<div class="footer-col abs" style="left:383px;top:3460px">
  <h5>Quick Links</h5>
  <ul><li>Home</li><li>Featured Cities</li><li>Property Search</li><li>Email Alerts</li><li>Communities</li><li>Buyers &amp; Sellers</li></ul>
</div>
<div class="footer-col abs" style="left:597px;top:3460px">
  <h5>Other Links</h5>
  <ul><li>Rentals</li><li>Investing</li><li>Contact</li><li>Terms &amp; Conditions</li><li>privacy Policy</li></ul>
</div>
<div class="footer-col abs" style="left:811px;top:3460px">
  <h5>Newsletter</h5>
  <div class="email-field">E-mail id...</div>
  <div class="subscribe">SUBSCRIBE</div>
</div>
<div class="footer-rule abs"></div>
<p class="copyright abs">Copyrights © 2018. All Rights Reserved</p>

</body>
</html>
```